Letterhead designs for Property Management firm

Would like to see some different letterhead/envelope designs We are a residential property management company. We would like to see designs that utilize blue/grays/black

```html
<!DOCTYPE html>
<html lang="en">
<head>
<meta charset="utf-8">
<title>Harborview Property Management – Letterhead</title>
<link rel="stylesheet" href="https://fonts.googleapis.com/css2?family=Arimo:wght@400;700&display=swap">
<style>
  :root {
    --backdrop: #e4e6ea;
    --paper: #ffffff;
    --ink: #5a5d63;
    --ink-strong: #4a4d52;
    --brand-blue: #1c4fa3;
    --brand-navy: #123d85;
    --brand-soft: #6f86c4;
    --on-brand: #ffffff;
  }
  * { box-sizing: border-box; margin: 0; padding: 0; }
  html, body {
    width: 1200px; height: 1200px; overflow: hidden;
    background: var(--backdrop);
    font-family: "Arimo", Arial, sans-serif;
  }
  .letterhead {
    position: absolute; left: 197px; top: 30px;
    width: 806px; height: 1140px;
    background: var(--paper);
    box-shadow: 0 6px 24px rgba(0,0,0,.18);
    overflow: hidden;
    color: var(--ink);
    font-size: 13.5px;
  }
  .brand-name {
    position: absolute; left: 86px; top: 52px;
    display: flex; align-items: center; gap: 10px;
    color: var(--brand-blue); font-weight: 700;
    font-size: 22px; line-height: 1.1; letter-spacing: .5px;
  }
  .brand-name .mark { width: 14px; height: 14px; background: var(--brand-blue); flex: none; }
  .letter { position: absolute; left: 86px; width: 640px; line-height: 18.9px; }
  .date { top: 265px; }
  .recipient { top: 321px; }
  .recipient strong, .sign-off strong { color: var(--ink-strong); font-weight: 700; }
  .salutation { top: 416px; }
  .body-text { top: 455px; text-align: justify; }
  .body-text p + p { margin-top: 18.9px; }
  .sign-off { top: 815px; }
  .signature {
    width: 175px; height: 20px; margin: 0 0 0 2px;
    background: linear-gradient(90deg, rgba(40,40,40,.55), rgba(40,40,40,.25));
    border-radius: 10px;
  }
  .footer-art { position: absolute; left: 0; top: 0; width: 806px; height: 1140px; }
  .contact {
    position: absolute; right: 37px; top: 1028px;
    text-align: right; color: var(--on-brand); font-size: 13.5px; line-height: 16.5px;
  }
  .contact li { list-style: none; display: flex; justify-content: flex-end; align-items: center; gap: 8px; }
  .contact svg { width: 10px; height: 10px; }
  .company-block {
    position: absolute; right: 37px; top: 1091px;
    text-align: right; color: var(--on-brand); line-height: 17px; font-size: 13.5px;
  }
  .company-block strong { font-weight: 700; }
</style>
</head>
<body>
<main class="letterhead">
  <svg class="footer-art" viewBox="0 0 838 1185" preserveAspectRatio="none" aria-hidden="true">
    <defs>
      <linearGradient id="wave-soft" x1="0" y1="0" x2="1" y2="0">
        <stop offset="0" stop-color="#dfe3f2" stop-opacity=".2"/>
        <stop offset="1" stop-color="#b9c3e6"/>
      </linearGradient>
      <linearGradient id="wave-main" x1="0" y1="0" x2="1" y2="0">
        <stop offset="0" stop-color="#1a4fa6"/>
        <stop offset=".55" stop-color="#5a74bd"/>
        <stop offset="1" stop-color="#6c83c6"/>
      </linearGradient>
    </defs>
    <path d="M0 1110 C260 1180 560 1110 838 860 L838 1185 L0 1185Z" fill="url(#wave-soft)"/>
    <path d="M0 1112 C240 1170 560 1100 838 930 L838 1185 L0 1185Z" fill="url(#wave-main)"/>
    <path d="M0 1105 C240 1160 560 1090 838 925" fill="none" stroke="#ffffff" stroke-width="6" opacity=".85"/>
    <path d="M0 1135 C260 1175 560 1115 838 985" fill="none" stroke="#c9d2ee" stroke-width="4" opacity=".7"/>
    <path d="M0 1150 C280 1185 560 1135 838 1010" fill="none" stroke="#0f3f8f" stroke-width="14" opacity=".6"/>
    <rect x="0" y="1120" width="838" height="65" fill="#1a52a8"/>
    <path d="M0 1120 C300 1150 560 1130 838 1090 L838 1120Z" fill="#1a52a8"/>
  </svg>

  <div class="brand-name"><span class="mark"></span><span>HARBORVIEW<br>PROPERTY MANAGEMENT</span></div>

  <p class="letter date">January 1, 2050</p>
  <address class="letter recipient" style="font-style:normal">
    <strong>Martin Hale</strong><br>
    Managing Director<br>
    Co.Street, Building/Suite<br>
    City/State, Zip Code
  </address>
  <p class="letter salutation">Dear Owen Prescott,</p>
  <div class="letter body-text">
    <p>Lorem ipsum dolor sit amet, consectetuer adipiscing elit, sed diam nonummy nibh euismod tincidunt ut laoreet dolore magna aliquam erat volutpat. Ut wisi enim ad minim veniam, quis nostrud exerci tation ullamcorper suscipit lobortis nisl ut aliquip ex ea commodo consequat. Duis dolore te feugait nulla facilisi. Nam liber tempor cum soluta nobis eleifend option congue nihil imperdiet doming id quod mazim placerat facer possim assum. Lorem ipsum dolor sit amet, consectetuer adipiscing elit, sed diam nonummy nibh euismod tincidunt ut laoreet dolore magna aliquam erat volutpat. Ut wisi enim ad minim veniam, quis nostrud exerci tation ullamcorper suscipit lobortis nisl ut aliquip ex ea commodo consequat.</p>
    <p>Consectetuer adipiscing elit, sed diam nonummy nibh euismod tincidunt ut laoreet dolore magna aliquam erat volutpat. Ut wisi enim ad minim veniam, quis nostrud exerci tation ullamcorper suscipit lobortis nisl ut aliquip ex ea commodo consequat. Consectetuer adipiscing elit, sed diam nonummy nibh euismod tincidunt ut laoreet dolore magna aliquam erat volutpat. Ut wisi enim ad minim veniam, quis nostrud exerci tation ullamcorper suscipit lobortis nisl ut aliquip ex ea commodo consequat.</p>
    <p>Duis dolore te feugait nulla facilisi. Nam liber tempor cum soluta nobis eleifend option congue nihil imperdiet doming id quod mazim placerat facer possim assum.Duis dolore te feugait nulla facilisi. Nam liber tempor cum soluta nobis eleifend option congue nihil imperdiet doming id quod mazim placerat facer possim assum.</p>
  </div>
  <div class="letter sign-off">
    Sincerely Yours,
    <div class="signature" role="img" aria-label="Handwritten signature of the managing director"></div>
    <strong>Authorized Managing Director</strong><br>
    Your Company Name
  </div>

  <ul class="contact">
    <li>300.555.0142
      <svg viewBox="0 0 10 10"><path d="M2 1 L4 3 L3 4 Q4 6 6 7 L7 6 L9 8 L8 9 Q3 9 1 2Z" fill="#fff"/></svg></li>
    <li>info@harborviewproperty.com
      <svg viewBox="0 0 10 10"><rect x="1" y="2.5" width="8" height="5.5" fill="none" stroke="#fff"/><path d="M1 2.5 L5 6 L9 2.5" fill="none" stroke="#fff"/></svg></li>
    <li>www.harborviewproperty.com
      <svg viewBox="0 0 10 10"><circle cx="5" cy="5" r="4" fill="none" stroke="#fff"/><path d="M1 5 H9 M5 1 V9" stroke="#fff"/></svg></li>
  </ul>
  <div class="company-block">
    <strong>HARBORVIEW PROPERTY MANAGEMENT</strong><br>
    Co.Street, Building/Suite 12345, City/State, Zip Code
  </div>
</main>
</body>
</html>
```